Web design project for exciting Australian start-up

Background
We are looking for a creative and talented web design artist to work alongside our market leading web developer.
• You will be required to create a modern and clean design theme for our website, incorporating selected rustic colour scheme elements for our exciting Australian start-up to operate within the coffee industry.
reoccurring work to be expected to flow to the successful designer.
Requirements
• c. 5 - 10 page website
• Landing page
• Log in/ out
• 404 template
• Typography is emphasised
• Please use either a) typemarrow.com, b) free web fonts, c) brindle fonts
• All design elements in vector format
• Preferably with icons for each header title(i.e. about us, how it works etc) but designer have free reign over how the site looks, so might not be applicable
• All pages to be responsive
• Down to eSlab resolution

High level visual design brief attached - additional pages to be worked from base design.

Design inspiration
• We would like to use design elements from the following sources:
http://www.zandrix.com/halcyon/ (Functionality)
Colour scheme refer to logo and complementary style guide

```html
<!DOCTYPE html>
<html lang="en">
<head>
<meta charset="utf-8">
<title>Bean Harbour — Coffee Marketplace</title>
<link href="https://fonts.googleapis.com/css2?family=Josefin+Sans:wght@600;700&family=Josefin+Slab:wght@400;600&display=swap" rel="stylesheet">
<style>
:root{
  --orange:#ff9f38;
  --red:#ec3b3f;
  --ink:#222;
  --muted:#4a4a4a;
  --nav-line:#ececec;
  --nav-bg:#fafafa;
  --footer-bg:#262626;
  --footer-text:#e6e6e6;
  --footer-line:#5a5a5a;
  --white:#fff;
}
*{box-sizing:border-box;margin:0;padding:0}
html,body{width:1200px;height:950px;overflow:hidden}
body{font-family:"Josefin Slab",serif;background:var(--white);color:var(--ink);position:relative}
.site-header{position:absolute;top:0;left:0;width:1200px;height:107px;background:var(--white)}
.brand{position:absolute;left:161px;top:22px;display:flex;align-items:center;gap:10px;
  font-family:"Josefin Sans",sans-serif;font-weight:700;font-size:25px;color:var(--ink);letter-spacing:1px;text-transform:uppercase}
.brand-mark{width:60px;height:60px;border-radius:50%;border:3px solid var(--ink);background:var(--orange)}
.main-nav{position:absolute;left:563px;top:0;height:107px;display:flex}
.main-nav a{display:flex;flex-direction:column;align-items:center;justify-content:center;gap:8px;
  height:107px;border-left:1px solid var(--nav-line);text-decoration:none;color:var(--muted);
  font-size:13px;text-transform:uppercase;letter-spacing:.3px}
.main-nav a:last-child{border-right:1px solid var(--nav-line)}
.main-nav .about{width:94px;background:var(--nav-bg)}
.main-nav .how{width:132px}
.main-nav .faq{width:66px}
.main-nav svg{width:20px;height:20px}
.auth{position:absolute;top:38px;left:878px;display:flex;gap:9px}
.btn{display:inline-flex;align-items:center;justify-content:center;color:var(--white);text-decoration:none;border-radius:3px}
.auth .btn{width:76px;height:31px;font-size:14px}
.btn-login{background:var(--orange)}
.btn-signup{background:var(--red)}
.hero{position:absolute;top:107px;left:0;width:1200px;height:543px;
  background:radial-gradient(ellipse at 62% 40%,#c97a4a 0%,#8e4a26 35%,#5a2e18 70%,#3a1d10 100%);
  text-align:center;color:var(--white)}
.hero-kicker{position:absolute;top:205px;width:100%;font-size:32px;font-weight:400;letter-spacing:.5px}
.hero-title{position:absolute;top:245px;width:100%;font-size:45px;font-weight:600;letter-spacing:1px}
.btn-video{position:absolute;left:519px;top:310px;width:162px;height:46px;background:var(--orange);
  font-size:20px;font-weight:600;letter-spacing:.5px}
.site-footer{position:absolute;top:650px;left:0;width:1200px;height:300px;background:var(--footer-bg);color:var(--footer-text)}
.footer-col{position:absolute;top:52px;width:140px}
.footer-col h3{font-family:"Josefin Sans",sans-serif;font-weight:700;font-size:17px;color:var(--white);margin-bottom:12px;white-space:nowrap}
.footer-col ul{list-style:none}
.footer-col li{height:31px;display:flex;align-items:center;gap:14px;border-bottom:1px solid var(--footer-line);font-size:15px}
.footer-col li:last-child{border-bottom:none}
.col-info{left:295px}
.col-who{left:548px}
.col-who h3{margin-left:-6px}
.col-join{left:799px}
.col-join li span.name{width:62px}
.social-dot{width:10px;height:10px;background:var(--footer-text);border-radius:2px}
.footer-rule{position:absolute;left:161px;top:241px;width:878px;border-top:1px solid var(--footer-line)}
.copyright{position:absolute;top:262px;width:100%;text-align:center;font-size:15px}
</style>
</head>
<body>
<header class="site-header">
  <div class="brand"><span>Bean</span><span class="brand-mark"></span><span>Harbour</span></div>
  <nav class="main-nav">
    <a class="about" href="#">
      <svg viewBox="0 0 20 20" fill="none" stroke="#ff9f38" stroke-width="1.5"><path d="M3 10 L10 3 L17 10 M5 8 V17 H15 V8 M8 17 V12 H12 V17"/></svg>
      About us</a>
    <a class="how" href="#">
      <svg viewBox="0 0 20 20" fill="none" stroke="#777" stroke-width="1.3"><circle cx="7" cy="8" r="2.5"/><path d="M2 18 Q7 11 12 18"/><rect x="10" y="2" width="8" height="6"/></svg>
      How it works</a>
    <a class="faq" href="#">
      <svg viewBox="0 0 20 20" fill="none" stroke="#777" stroke-width="1.3"><rect x="3" y="5" width="4" height="12"/><rect x="9" y="3" width="3" height="14"/><rect x="14" y="3" width="3" height="14"/></svg>
      FAQ</a>
  </nav>
  <div class="auth">
    <a class="btn btn-login" href="#">Login</a>
    <a class="btn btn-signup" href="#">Sign up</a>
  </div>
</header>

<section class="hero" role="img" aria-label="Photo of a cup of coffee on a saucer with a wooden coffee grinder and scattered roasted beans">
  <p class="hero-kicker">Australia first online</p>
  <h1 class="hero-title">COFFEE MARKETPLACE</h1>
  <a class="btn btn-video" href="#">Watch Video</a>
</section>

<footer class="site-footer">
  <div class="footer-col col-info">
    <h3>HELPFUL INFO</h3>
    <ul><li>About Us</li><li>Media Enquiries</li><li>Terms &amp; Conditions</li><li>Privacy Policy</li></ul>
  </div>
  <div class="footer-col col-who">
    <h3>WHO WE ARE</h3>
    <ul><li>How it works</li><li>FAQ</li><li style="border-bottom:1px solid var(--footer-line)">Contact us</li></ul>
  </div>
  <div class="footer-col col-join">
    <h3>JOIN US ON</h3>
    <ul>
      <li><span class="name">Friendlane</span><span class="social-dot"></span></li>
      <li><span class="name">Chirpline</span><span class="social-dot"></span></li>
      <li><span class="name">Workmesh</span><span class="social-dot"></span></li>
      <li><span class="name">Viewcast</span><span class="social-dot"></span></li>
    </ul>
  </div>
  <div class="footer-rule"></div>
  <p class="copyright">Copyright © 2014 Bean Harbour</p>
</footer>
</body>
</html>
```